Powerpoint design template for LUMOTEX for new digital platform

We would like to use a PowerPoint template, we would like to create a new page, we would like to create a new digital platform LUMOTEX for schools and parents for the creation of playful communication and educational tools for children to enhance their positive development, amaze them learn in a playful way. This platform is going to be the most creative, stimulating and innovative classroom, easy to use and fast to implement. Scrapbooking, collages ... Magazine, newsletters Diplomla / awards Slideshows Facebook Calendars Organizers Greetings Games ... This powerpoint template will be used essential to We are looking for a professional design, positioning our brand in the children market with an adult hearing. so you will need to find a good deal. Primary target: nurseries & schools from 0 to 18 years old and universities (in 2nd phase) Secondary target: small & medium businesses Third target: general public, and TPE If it is a color scheme, then it is suggested that it be marketed in Europe (UK, Italy, Spain) and in a 2nd Stage USA and other countries. multiple options for front page, insidious pages (multiple styles with limited text and extended text) and final contact page We need something to read, we can not do it too much, but we can not do it. , and inside pages aligned to our logo

Target Market(s)

Target 1; Education with teacher Target 2; parents and grandparents

Industry/Entity Type

Education

Font styles to use
Other font styles liked:
• not decided. but not too fancy

Requirements
Must have
• Multi page options for front page, page insides (multiple styles with limited text and extended text) and final page contact
Nice to have
• do not have a lot of ideas. We need something to read, we can not get away from it
Should not have
• not too fancy and busy: keep clarity & simplicity while reassuring on quality

```html
<!DOCTYPE html>
<html lang="en">
<head>
<meta charset="utf-8">
<title>Lumotex – Slide</title>
<link rel="stylesheet" href="https://fonts.googleapis.com/css2?family=Oswald:wght@500;600&family=Raleway:wght@400;600&family=Roboto+Condensed:wght@400&display=swap">
<style>
  :root {
    --lime: #d9e141;
    --lime-deep: #b6cf2c;
    --lime-pale: #e8ee7a;
    --orange: #f7941d;
    --gold: #f5b324;
    --ink: #2b2b2b;
    --body: #3a3a3a;
    --paper: #ffffff;
    --book: #8e6bb7;
  }
  * { margin: 0; padding: 0; box-sizing: border-box; }
  html, body { width: 1200px; height: 900px; overflow: hidden; background: var(--paper); }
  .slide { position: relative; width: 1200px; height: 900px; overflow: hidden; background: var(--paper); }
  .bands { position: absolute; inset: 0; }
  .title {
    position: absolute; left: 30px; top: 26px;
    font-family: "Oswald", "Roboto Condensed", sans-serif; font-weight: 600;
    font-size: 46px; line-height: 60px; color: var(--ink); letter-spacing: 0.5px;
  }
  .brand {
    position: absolute; left: 1000px; top: 42px;
    display: flex; align-items: center; gap: 10px;
    font-family: "Oswald", sans-serif; font-weight: 600; font-size: 30px; color: var(--ink);
  }
  .brand-mark { width: 18px; height: 18px; background: var(--orange); }
  .book-icon { position: absolute; left: 56px; top: 186px; width: 52px; height: 56px; }
  .content { position: absolute; left: 133px; top: 186px; width: 490px; }
  .subtitle {
    font-family: "Raleway", sans-serif; font-weight: 600;
    font-size: 30px; line-height: 42px; color: var(--gold);
  }
  .content p {
    font-family: "Raleway", sans-serif; font-weight: 400;
    font-size: 22.5px; line-height: 36px; color: var(--body);
  }
  .content p + p { margin-top: 36px; }
  .photo {
    position: absolute; left: 630px; top: 183px; width: 570px; height: 590px;
    background: linear-gradient(90deg, #ffffff 0%, #f4e6dc 18%, #e9c9b3 45%, #caa080 75%, #8b6a54 100%);
  }
  .footer-url, .page-number {
    position: absolute; top: 848px;
    font-family: "Roboto Condensed", sans-serif; font-size: 25px; line-height: 36px; color: var(--ink);
  }
  .footer-url { left: 20px; }
  .page-number { left: 1078px; }
</style>
</head>
<body>
<main class="slide">
  <svg class="bands" width="1200" height="900" viewBox="0 0 1200 900" aria-hidden="true">
    <polygon points="0,0 960,0 915,110 0,110" fill="var(--lime)"/>
    <polygon points="960,0 978,0 930,108 912,110" fill="var(--lime-deep)"/>
    <polygon points="978,0 990,0 945,96 935,100" fill="var(--lime-pale)"/>
    <polygon points="0,834 975,834 1000,900 0,900" fill="var(--lime)"/>
    <polygon points="975,834 990,834 1028,900 1000,900" fill="var(--lime-deep)"/>
    <polygon points="998,834 1200,834 1200,900 1040,900" fill="var(--orange)"/>
  </svg>

  <h1 class="title">PROJECT TITLE HERE</h1>

  <div class="brand"><span class="brand-mark"></span><span>LUMOTEX</span></div>

  <svg class="book-icon" viewBox="0 0 52 56" aria-hidden="true">
    <g transform="rotate(-14 26 28)">
      <rect x="10" y="6" width="30" height="42" rx="3" fill="var(--book)"/>
      <rect x="10" y="44" width="30" height="6" rx="2" fill="#cbb8e2"/>
      <rect x="10" y="6" width="5" height="44" fill="#6f4f99"/>
    </g>
  </svg>

  <section class="content">
    <h2 class="subtitle">Subtext here</h2>
    <p>Lemon drops oat cake oat cake sugar plum sweet gingerbread chocolate cake ginger-bread. Lemon drops oat cake oat cake sugar plum sweet Lemon drops oat cake oat cake sugar plum sweet gingerbread chocolate cake gingerbread. Lemon drops oat cake oat cake sugar plum sweet</p>
    <p>Lemon drops oat cake oat cake sugar plum sweet gingerbread chocolate cake ginger-bread. Lemon drops oat cake oat cake sugar plum sweet</p>
  </section>

  <div class="photo" role="img" aria-label="Photo of a smiling child holding up a hand covered in bright paint"></div>

  <div class="footer-url">www.lumotex.com</div>
  <div class="page-number">Page : 01</div>
</main>
</body>
</html>
```